Im open to ideas.. I was thinking on my business cards aswell as my logo. a place for my name. email. phone number and abn..

ive attched a file with my business logo. which i dont love the colours.. i was think a dark background with charcoal letters so something along those colour schumes but im open to ideas..

BRM Constructions

```html
<!DOCTYPE html>
<html lang="en">
<head>
<meta charset="utf-8">
<title>BRM Constructions – Business Card</title>
<link rel="stylesheet" href="https://fonts.googleapis.com/css2?family=Montserrat:wght@400;500;700&display=swap">
<style>
  :root {
    --stage: #d9d4cc;
    --card-black: #0b0b0c;
    --card-sheen: #2a2a2c;
    --brand-red: #e0202b;
    --brand-red-dark: #b3121b;
    --paper-white: #f4f4f4;
    --text-light: #eeeeee;
    --text-muted: #bdbdbd;
  }
  * { box-sizing: border-box; margin: 0; padding: 0; }
  html, body { width: 1200px; height: 1022px; overflow: hidden; }
  body {
    background: var(--stage);
    font-family: "Montserrat", Arial, sans-serif;
    position: relative;
  }
  .card {
    position: absolute;
    left: 300px;
    width: 600px;
    height: 343px;
    background: linear-gradient(160deg, var(--card-sheen) 0%, var(--card-black) 45%, var(--card-black) 100%);
    border-radius: 4px;
    overflow: hidden;
    box-shadow: 0 14px 30px rgba(0,0,0,.28);
  }
  .card--front { top: 110px; }
  .card--back  { top: 569px; }

  .card__band {
    position: absolute;
    left: 0; bottom: 0;
    width: 100%;
    height: 78px;
  }

  /* Front: brand name */
  .brand {
    position: absolute;
    left: 0; right: 0; top: 104px;
    display: flex;
    align-items: center;
    justify-content: center;
    gap: 16px;
  }
  .brand__mark {
    width: 26px; height: 26px;
    background: var(--brand-red);
  }
  .brand__name {
    color: var(--text-light);
    font-weight: 700;
    font-size: 38px;
    letter-spacing: 2px;
    text-transform: uppercase;
  }

  /* Back: contact details */
  .tab {
    position: absolute;
    top: 0; right: 34px;
    width: 56px; height: 22px;
    background: var(--paper-white);
  }
  .contact {
    position: absolute;
    top: 46px; right: 40px;
    text-align: right;
    color: var(--text-light);
  }
  .contact__name {
    color: var(--brand-red);
    font-weight: 500;
    font-size: 27px;
    letter-spacing: 1px;
    text-transform: uppercase;
  }
  .contact__role {
    font-size: 16px;
    margin-top: 2px;
    margin-bottom: 14px;
  }
  .contact__row {
    display: flex;
    justify-content: flex-end;
    align-items: center;
    gap: 10px;
    font-size: 16px;
    line-height: 26px;
  }
  .contact__label { color: var(--brand-red); font-weight: 500; }
  .contact__icon { width: 13px; height: 13px; flex: none; }
  .contact__spacer { width: 13px; flex: none; }
</style>
</head>
<body>

<section class="card card--front" aria-label="Business card front">
  <div class="brand">
    <span class="brand__mark"></span>
    <span class="brand__name">BRM Constructions</span>
  </div>
  <svg class="card__band" viewBox="0 0 600 78" preserveAspectRatio="none" aria-hidden="true">
    <rect x="0" y="20" width="600" height="22" fill="var(--brand-red)"/>
    <rect x="0" y="42" width="600" height="36" fill="var(--paper-white)"/>
  </svg>
</section>

<section class="card card--back" aria-label="Business card back">
  <div class="tab"></div>
  <div class="contact">
    <p class="contact__name">Marcus Hale</p>
    <p class="contact__role">Director</p>
    <p class="contact__row"><span><span class="contact__label">ABN</span>: 61 482 305 719</span><span class="contact__spacer"></span></p>
    <p class="contact__row">+330 2481-7093
      <svg class="contact__icon" viewBox="0 0 16 16" aria-hidden="true"><path d="M4 1l3 3-2 2c1 2 3 4 5 5l2-2 3 3-2 3C7 15 1 9 1 3z" fill="var(--brand-red)"/></svg>
    </p>
    <p class="contact__row">info@brmconstructions.com
      <svg class="contact__icon" viewBox="0 0 16 16" aria-hidden="true"><rect x="1" y="3" width="14" height="10" fill="none" stroke="var(--brand-red)" stroke-width="2"/><path d="M1 3l7 6 7-6" fill="none" stroke="var(--brand-red)" stroke-width="2"/></svg>
    </p>
    <p class="contact__row">www.brmconstructions.com
      <svg class="contact__icon" viewBox="0 0 16 16" aria-hidden="true"><circle cx="8" cy="8" r="7" fill="var(--brand-red)"/><path d="M1 8h14M8 1c3 3 3 11 0 14M8 1c-3 3-3 11 0 14" fill="none" stroke="var(--card-black)" stroke-width="1"/></svg>
    </p>
  </div>
  <svg class="card__band" viewBox="0 0 600 78" preserveAspectRatio="none" aria-hidden="true">
    <rect x="0" y="20" width="600" height="22" fill="var(--brand-red)"/>
    <rect x="0" y="42" width="600" height="36" fill="var(--paper-white)"/>
  </svg>
</section>

</body>
</html>
```